Dultavo.com webside

I want to build a Dultavo.com retail website use on Shopify, reselling three main categories: Office Supplies, Packing Supplies, and Home Consumables. I also wish the webpage has the same functions as the Zelvik home page. The page is split into three different parts with the top being a sliding screen showcasing promotion products, below it being the three categories, and finally, a moving screen showing company missions.
Target Market(s)
U.S online
Industry/Entity Type
Office Supplies, packing Supplies and Home Consumables
Coding
Coded - Design and coding required
Number of Pages Required
5+ page
Look and feel

```html
<!DOCTYPE html>
<html lang="en">
<head>
<meta charset="utf-8">
<title>Dultavo – Office, Packing &amp; Home Consumables</title>
<link rel="stylesheet" href="https://fonts.googleapis.com/css2?family=Outfit:wght@300;400;500;600;700;800&display=swap">
<style>
:root{
  --brand:#4cc4ae;
  --brand-deep:#18b4a1;
  --nav:#55c3b0;
  --mission:#1ab4a2;
  --ink:#222;
  --muted:#666;
  --soft-band:#e9f7f5;
  --foot-band:#eef8f7;
  --star:#f5c518;
  --line:#dcdcdc;
}
*{box-sizing:border-box;margin:0;padding:0}
html,body{width:1200px;height:3306px;overflow:hidden}
body{position:relative;font-family:"Outfit",sans-serif;color:var(--ink);background:#fff}
.abs{position:absolute}
a{color:inherit;text-decoration:none}

/* header */
.site-header{left:0;top:0;width:1200px;height:99px;background:#fff}
.logo{font-family:"Outfit",sans-serif;font-weight:600;color:var(--brand);font-size:42px;letter-spacing:-.5px;line-height:1}
.site-header .logo{left:105px;top:27px}
.search{left:357px;top:28px;width:448px;height:44px;border:1.5px solid var(--brand);display:flex;align-items:center;font-size:12px;color:#555}
.search .cat{width:138px;height:100%;border-right:1.5px solid var(--brand);display:flex;align-items:center;justify-content:space-between;padding:0 12px}
.search .kw{flex:1;padding:0 14px}
.search svg{margin-right:12px}
.head-icon{width:42px;height:42px;border-radius:50%;background:#d9f3ee;display:flex;align-items:center;justify-content:center;top:28px}
.head-icon.cart{background:var(--brand)}
.cart-badge{right:-6px;top:-6px;width:16px;height:16px;border-radius:50%;background:var(--brand-deep);border:2px solid #fff;color:#fff;font-size:9px;display:flex;align-items:center;justify-content:center}

.main-nav{left:0;top:99px;width:1200px;height:58px;background:var(--nav)}
.main-nav a{position:absolute;top:21px;color:#fff;font-size:13px;letter-spacing:.2px;transform:translateX(-50%)}
.main-nav a.active::after{content:"";position:absolute;left:-13px;right:-13px;top:33px;height:3px;background:#fff}

/* hero */
.hero{left:0;top:157px;width:1200px;height:557px}
.hero-photo{position:absolute;inset:0;background:linear-gradient(90deg,#f4f4f3 0%,#ecebea 38%,#e3d7c6 55%,#d25a3a 75%,#e4562e 88%,#ddd 100%)}
.hero-text{left:108px;top:90px}
.hero h1{font-weight:300;font-size:42px;line-height:50px;color:#222}
.hero h1 strong{display:block;font-weight:700;color:var(--brand);font-size:47px;line-height:51px}
.hero .offer{margin-top:10px;font-size:19px;color:#222}
.hero .offer b{font-weight:800}
.hero .promo{margin-top:8px;display:flex;align-items:center;gap:12px;color:var(--brand);font-weight:700;font-size:17px}
.hero .promo span{background:#fff;color:var(--brand);font-size:13px;letter-spacing:1.5px;padding:6px 17px}
.btn{display:inline-flex;align-items:center;justify-content:center;gap:6px;background:var(--brand-deep);color:#fff;font-weight:600;border-radius:20px}
.hero .btn{margin-top:24px;width:135px;height:36px;font-size:13px}
.slide-arrow{width:24px;height:24px}

/* section headings */
.section-title{left:0;width:1200px;text-align:center;font-size:31px;font-weight:400;color:#222}
.section-title strong{font-weight:700;color:var(--brand)}
.section-title::after{content:"";display:block;width:48px;height:2px;background:var(--brand);margin:8px auto 0}

/* categories */
.cat-photo{top:861px;width:319px;height:240px;border-radius:3px}
.cat-card{top:1054px;width:290px;height:128px;background:#fff;box-shadow:0 1px 5px rgba(0,0,0,.15);text-align:center;padding-top:16px}
.cat-card.is-hover{border-bottom:3px solid var(--brand-deep)}
.cat-card h3{font-size:18px;font-weight:500;color:#222}
.cat-card p{font-size:11px;line-height:15px;color:#555;margin:6px 20px 0}
.cat-card .btn{margin-top:10px;width:118px;height:31px;font-size:9px}

/* mission */
.mission{left:0;top:1260px;width:1200px;height:547px;background:var(--mission);color:#fff}
.mission-ring{left:145px;top:65px;width:432px;height:432px;border-radius:50%;border:3px solid #fff}
.mission-photo{left:156px;top:76px;width:410px;height:410px;border-radius:50%;background:radial-gradient(circle at 55% 45%,#f2f2f0 0%,#dcdcda 45%,#c9a77a 80%,#b98f5e 100%)}
.mission h2{left:629px;top:125px;font-size:41px;font-weight:300}
.mission h2 strong{font-weight:700}
.mission h2::after{content:"";display:block;width:54px;height:2px;background:#fff;margin-top:6px}
.mission p{left:633px;width:455px;font-size:17.5px;line-height:25.5px;font-weight:300}

/* products */
.product{top:1974px;width:227px;height:318px;background:#fff;box-shadow:0 1px 8px rgba(0,0,0,.08);text-align:center}
.product-photo{position:absolute;left:34px;top:30px;width:160px;height:150px;border-radius:4px}
.product h4{position:absolute;left:0;right:0;top:226px;font-size:15px;font-weight:400;color:#222}
.stars{color:var(--star);letter-spacing:4px;font-size:13px}
.product .stars{position:absolute;left:0;right:0;top:247px}
.product .price{position:absolute;left:0;right:0;top:266px;color:var(--brand-deep);font-size:18px;font-weight:600}

/* testimonials */
.reviews{left:0;top:2404px;width:1200px;height:490px;background:var(--soft-band)}
.reviews h2{left:122px;top:140px;font-size:34px;font-weight:300;line-height:42px;color:#222}
.reviews h2 strong{display:block;font-weight:700;color:var(--brand)}
.reviews .lead{left:122px;top:244px;width:310px;font-size:14px;line-height:24px;color:#555}
.review-card{top:108px;width:284px;height:252px;background:#fff;border:1.5px solid var(--line);padding:22px 28px}
.quote-mark{font-size:54px;line-height:40px;color:#cfcfcf;font-weight:800;font-family:Georgia,serif}
.review-card p{margin-top:16px;font-size:11.5px;line-height:21px;font-style:italic;color:#555}
.review-author{margin-top:12px;display:flex;align-items:center;gap:10px}
.avatar{width:40px;height:40px;border-radius:50%;background:linear-gradient(135deg,#c9a48a,#7a5a48)}
.review-author b{display:block;font-size:12px;font-weight:600;color:#444}
.review-author .stars{font-size:11px;letter-spacing:2px}

/* footer */
.site-footer .logo{left:137px;top:2983px;font-size:48px}
.foot-about{left:137px;top:3045px;width:210px;font-size:11.5px;line-height:21px;color:#555}
.foot-col h5{font-size:15px;font-weight:600;color:#222;letter-spacing:.3px}
.foot-col h5::after{content:"";display:block;width:36px;height:2px;background:var(--brand);margin-top:7px}
.foot-col ul{list-style:none;margin-top:10px}
.foot-col li{font-size:11px;color:#555;line-height:26px}
.contact-row{display:flex;align-items:center;gap:12px;margin-top:14px}
.contact-icon{width:34px;height:34px;border-radius:50%;background:var(--brand-deep);display:flex;align-items:center;justify-content:center}
.contact-row small{display:block;font-size:11px;color:var(--brand-deep)}
.contact-row span{font-size:13px;color:#333}
.foot-bar{left:0;top:3243px;width:1200px;height:63px;background:var(--foot-band);font-size:10.5px;color:#444}
.foot-bar .copy{position:absolute;left:136px;top:26px}
.foot-bar nav{position:absolute;left:782px;top:22px;display:flex;gap:15px}
</style>
</head>
<body>

<header class="site-header abs">
  <div class="logo abs">Dultavo</div>
  <div class="search abs">
    <div class="cat">All Categories
      <svg width="10" height="6" viewBox="0 0 10 6"><path d="M1 1l4 4 4-4" fill="none" stroke="#4cc4ae" stroke-width="1.4"/></svg>
    </div>
    <div class="kw">Search Keyword</div>
    <svg width="15" height="15" viewBox="0 0 16 16"><circle cx="6.5" cy="6.5" r="5" fill="none" stroke="#18b4a1" stroke-width="2"/><path d="M10.5 10.5L15 15" stroke="#18b4a1" stroke-width="2"/></svg>
  </div>
  <div class="head-icon abs" style="left:920px">
    <svg width="20" height="18" viewBox="0 0 24 22"><path d="M12 20S2 13.5 2 7.5A5 5 0 0 1 12 5a5 5 0 0 1 10 2.5C22 13.5 12 20 12 20z" fill="none" stroke="#18b4a1" stroke-width="1.8"/></svg>
  </div>
  <div class="head-icon abs" style="left:971px">
    <svg width="18" height="20" viewBox="0 0 20 22"><circle cx="10" cy="6" r="4.5" fill="none" stroke="#18b4a1" stroke-width="1.8"/><path d="M2 21c0-5 3.6-8 8-8s8 3 8 8z" fill="none" stroke="#18b4a1" stroke-width="1.8"/></svg>
  </div>
  <div class="head-icon cart abs" style="left:1028px">
    <svg width="22" height="20" viewBox="0 0 24 22"><path d="M1 2h4l3 12h12l3-9H7" fill="none" stroke="#fff" stroke-width="1.8"/><circle cx="10" cy="18.5" r="1.8" fill="#fff"/><circle cx="18" cy="18.5" r="1.8" fill="#fff"/></svg>
    <div class="cart-badge abs">0</div>
  </div>
</header>

<nav class="main-nav abs">
  <a class="active" style="left:160px">HOME</a>
  <a style="left:280px">ABOUT US</a>
  <a style="left:430px">OUR PRODUCTS</a>
  <a style="left:587px">CATEGORIES</a>
  <a style="left:729px">SHOP NOW</a>
  <a style="left:859px">REVIEWS</a>
  <a style="left:988px">CONTACT US</a>
</nav>

<section class="hero abs">
  <div class="hero-photo" role="img" aria-label="Cleaning supplies on a wooden table: sponges, cloths, steel scourers, detergent bottles and a red bucket"></div>
  <div class="hero-text abs">
    <h1>Shop Home<strong>Consumables<br>Products</strong></h1>
    <p class="offer">GET UP TO <b>35% OF</b>F ON PRODUCTS</p>
    <p class="promo">USE PROMOCODE: <span>DULTAVO50</span></p>
    <a class="btn">Shop Now <svg width="8" height="10" viewBox="0 0 8 10"><path d="M2 1l4 4-4 4" fill="none" stroke="#fff" stroke-width="1.6"/></svg></a>
  </div>
  <svg class="slide-arrow abs" style="left:40px;top:230px" viewBox="0 0 24 24"><path d="M15 3L7 12l8 9" fill="none" stroke="#555" stroke-width="2.6"/></svg>
  <svg class="slide-arrow abs" style="left:1152px;top:230px" viewBox="0 0 24 24"><path d="M9 3l8 9-8 9" fill="none" stroke="#555" stroke-width="2.6"/></svg>
</section>

<h2 class="section-title abs" style="top:774px">Product <strong>Categories</strong></h2>

<div class="cat-photo abs" style="left:103px;background:linear-gradient(135deg,#f0ede8,#d9d6d0 60%,#c8a56a)" role="img" aria-label="Office supplies flat lay: pens, pencils, clips and sticky notes"></div>
<div class="cat-card abs" style="left:117px">
  <h3>Office Supplies</h3>
  <p>Lorem ipsum dolor sit amet, consectetur adipiscing elit ed do eiusmod</p>
  <a class="btn">View Products ›</a>
</div>

<div class="cat-photo abs" style="left:443px;background:linear-gradient(135deg,#c9b08a,#b59463 50%,#8a8f92)" role="img" aria-label="Packing tape dispenser sealing a cardboard box"></div>
<div class="cat-card is-hover abs" style="left:457px">
  <h3>Packing Supplies</h3>
  <p>Lorem ipsum dolor sit amet, consectetur adipiscing elit ed do eiusmod</p>
  <a class="btn">View Products ›</a>
</div>

<div class="cat-photo abs" style="left:783px;background:linear-gradient(135deg,#e8e9e6,#f5f5f3 55%,#b9c7a8)" role="img" aria-label="Kitchen counter with paper towel rolls"></div>
<div class="cat-card abs" style="left:797px">
  <h3>Home Consumables</h3>
  <p>Lorem ipsum dolor sit amet, consectetur adipiscing elit ed do eiusmod</p>
  <a class="btn">View Products ›</a>
</div>

<section class="mission abs">
  <div class="mission-ring abs"></div>
  <div class="mission-photo abs" role="img" aria-label="Warehouse workers in white coats and hairnets assembling cardboard boxes"></div>
  <h2 class="abs">Our <strong>Mission</strong></h2>
  <p class="abs" style="top:204px">Lorem ipsum dolor sit amet, consectetur adipiscing elit, sed do eiusmod tempor incididunt ut labore et dolore magna aliqua. Ut enim ad minim veniam, quis nostrud exercitation ullamco laboris nisi ut aliquip ex ea</p>
  <p class="abs" style="top:333px">Sed ut perspiciatis unde omnis iste natus error sit voluptatem accusantium doloremque laudanti</p>
  <svg class="slide-arrow abs" style="left:47px;top:259px" viewBox="0 0 24 24"><path d="M15 3L7 12l8 9" fill="none" stroke="#fff" stroke-width="2.8"/></svg>
  <svg class="slide-arrow abs" style="left:1143px;top:259px" viewBox="0 0 24 24"><path d="M9 3l8 9-8 9" fill="none" stroke="#fff" stroke-width="2.8"/></svg>
</section>

<h2 class="section-title abs" style="top:1874px">Popular <strong>Products</strong></h2>

<article class="product abs" style="left:109px">
  <div class="product-photo" style="background:linear-gradient(135deg,#f6b13a,#e85a4a 50%,#7ccc5a)" role="img" aria-label="Stack of colourful kitchen sponges"></div>
  <h4>Product Name/Title</h4><div class="stars">★★★★★</div><div class="price">$25.99</div>
</article>
<article class="product abs" style="left:357px">
  <div class="product-photo" style="background:linear-gradient(135deg,#c79d68,#a77b48 60%,#d7c29c)" role="img" aria-label="Cardboard box with packing tape roll"></div>
  <h4>Product Name/Title</h4><div class="stars">★★★★★</div><div class="price">$25.99</div>
</article>
<article class="product abs" style="left:605px">
  <div class="product-photo" style="background:linear-gradient(135deg,#ece6d6,#d4caae 55%,#f3efe5)" role="img" aria-label="Two rolls of clear packing tape"></div>
  <h4>Product Name/Title</h4><div class="stars">★★★★★</div><div class="price">$25.99</div>
</article>
<article class="product abs" style="left:853px">
  <div class="product-photo" style="background:linear-gradient(135deg,#fafafa,#e4e6e8 55%,#f4f4f4)" role="img" aria-label="Roll of white stretch wrap film"></div>
  <h4 style="top:222px">Product Name/Title</h4><div class="stars" style="top:243px">★★★★★</div><div class="price" style="top:262px">$25.99</div>
</article>

<section class="reviews abs">
  <h2 class="abs">What People are<strong>Syaing about us</strong></h2>
  <p class="lead abs">Lorem ipsum dolor sit amet, consectetur adipiscing elit, sed do eiusmod tempor</p>
  <svg class="abs" style="left:136px;top:330px" width="30" height="16" viewBox="0 0 30 16"><path d="M29 8H2M9 1L2 8l7 7" fill="none" stroke="#999" stroke-width="1.6"/></svg>
  <svg class="abs" style="left:180px;top:330px" width="30" height="16" viewBox="0 0 30 16"><path d="M1 8h27M21 1l7 7-7 7" fill="none" stroke="#222" stroke-width="1.6"/></svg>

  <div class="review-card abs" style="left:476px">
    <div class="quote-mark">“</div>
    <p>Lorem ipsum dolor sit amet, consectetur adipiscing elit, sed do eiusmod tempor incididunt ut labore et dolore magna aliqua. Ut enim ad minim veniam, quis nostrud exercitation ullamco laboris nisi ut</p>
    <div class="review-author"><div class="avatar" role="img" aria-label="Reviewer portrait"></div><div><b>By Author Name</b><span class="stars">★★★★★</span></div></div>
  </div>
  <div class="review-card abs" style="left:776px;top:106px">
    <div class="quote-mark">“</div>
    <p>Lorem ipsum dolor sit amet, consectetur adipiscing elit, sed do eiusmod tempor incididunt ut labore et dolore magna aliqua. Ut enim ad minim veniam, quis nostrud exercitation ullamco laboris nisi ut</p>
    <div class="review-author"><div class="avatar" role="img" aria-label="Reviewer portrait"></div><div><b>By Author Name</b><span class="stars">★★★★★</span></div></div>
  </div>
  <div class="review-card abs" style="left:1088px;top:106px">
    <div class="quote-mark">“</div>
    <p>Lorem ipsum dolor sit amet, consectetur adipiscing elit, sed do eiusmod tempor incididunt ut labore et dolore magna aliqua. Ut enim ad minim veniam, quis nostrud exercitation ullamco laboris nisi ut</p>
    <div class="review-author"><div class="avatar" role="img" aria-label="Reviewer portrait"></div><div><b>By Author Name</b><span class="stars">★★★★★</span></div></div>
  </div>
</section>

<footer class="site-footer">
  <div class="logo abs">Dultavo</div>
  <p class="foot-about abs">Lorem ipsum dolor sit amet, consectetur adipiscing elit, sed do eiusmod tempor Lorem ipsum dolor sit amet, consectetur adipiscing elit</p>
  <div class="foot-col abs" style="left:461px;top:2983px">
    <h5>NAVIGATION</h5>
    <ul><li>About Us</li><li>Products</li><li>Testimonials</li><li>Categories</li><li>Shop now</li></ul>
  </div>
  <div class="foot-col abs" style="left:666px;top:2983px">
    <h5>RESOURCES</h5>
    <ul><li>My Account</li><li>Cart</li><li>Support</li><li>Checkout</li><li>Contact Us</li></ul>
  </div>
  <div class="foot-col abs" style="left:865px;top:2983px">
    <h5 style="">CONTACT US</h5>
    <div class="contact-row">
      <div class="contact-icon"><svg width="16" height="16" viewBox="0 0 24 24"><path d="M5 3h4l2 5-2.5 1.5a11 11 0 0 0 6 6L16 13l5 2v4a2 2 0 0 1-2 2A17 17 0 0 1 3 5a2 2 0 0 1 2-2z" fill="none" stroke="#fff" stroke-width="1.8"/></svg></div>
      <div><small>Email address</small><span>support@dultavo.shop</span></div>
    </div>
    <div class="contact-row">
      <div class="contact-icon"><svg width="16" height="14" viewBox="0 0 24 18"><rect x="1.5" y="1.5" width="21" height="15" rx="1.5" fill="none" stroke="#fff" stroke-width="1.8"/><path d="M2 2l10 8 10-8" fill="none" stroke="#fff" stroke-width="1.8"/></svg></div>
      <div><small>Phone number</small><span>+1 555 014 2290</span></div>
    </div>
  </div>
  <div class="foot-bar abs">
    <span class="copy">© 2022 Company Name | All Rights Reserved</span>
    <nav><a>Terms &amp; Conditions</a><a>Contact</a><a>Privacy Policy</a><a>Help Center</a></nav>
  </div>
</footer>

</body>
</html>
```